Water ATM Card

Need a design for water ATM cards. Size of card is 3.375 x 2.125 inch
On the Front include the Cedar hollow Logo.
Bottom right corner should have Price $100
On the Back
This card is to be used to access water refills at any Cedar Hollow Water Vending Machines.
Please contact (869) 418 2930 or (869) 534 1276 or email clearflowbox@mailvista.example for any assistance or recharging of card.

```html
<!DOCTYPE html>
<html lang="en">
<head>
<meta charset="utf-8">
<title>Cedar Hollow Water Card</title>
<link href="https://fonts.googleapis.com/css2?family=Montserrat:wght@400;500;700;800&display=swap" rel="stylesheet">
<style>
  :root {
    --stage: #b3b3b3;
    --card-white: #ffffff;
    --brand-blue: #24469c;
    --brand-green: #3aa13c;
    --ink: #1e1e1e;
    --back-top: #3c69ab;
    --back-bottom: #2b3f95;
    --back-text: #e8eefb;
  }
  * { margin: 0; padding: 0; box-sizing: border-box; }
  html, body { width: 1200px; height: 900px; overflow: hidden; }
  body {
    background: var(--stage);
    font-family: "Montserrat", sans-serif;
    display: flex;
    flex-direction: column;
    align-items: center;
    justify-content: center;
    gap: 36px;
  }
  .card {
    width: 640px;
    height: 403px;
    position: relative;
    overflow: hidden;
    box-shadow: 0 6px 18px rgba(0,0,0,.25);
  }

  /* Front */
  .card-front { background: var(--card-white); }
  .brand-name {
    position: absolute;
    top: 58px; right: 48px;
    font-weight: 800;
    font-size: 30px;
    letter-spacing: 1px;
    color: var(--brand-blue);
    text-transform: uppercase;
  }
  .price {
    position: absolute;
    top: 138px; right: 48px;
    font-weight: 800;
    font-size: 34px;
    color: var(--brand-green);
  }
  .divider {
    position: absolute;
    top: 192px; left: 40px; right: 30px;
    height: 2px;
    background: var(--brand-blue);
  }
  .holder {
    position: absolute;
    top: 130px; left: 48px;
  }
  .holder-name {
    font-weight: 800;
    font-size: 24px;
    color: var(--brand-blue);
    text-transform: uppercase;
    letter-spacing: .5px;
  }
  .holder-role {
    font-size: 15px;
    color: var(--ink);
    margin-top: 4px;
  }
  .contacts {
    position: absolute;
    top: 216px; left: 48px;
    list-style: none;
    font-size: 15px;
    color: var(--ink);
  }
  .contacts li {
    display: flex;
    align-items: center;
    gap: 10px;
    height: 30px;
  }
  .contacts svg { width: 16px; height: 16px; fill: var(--brand-blue); flex: none; }
  .address {
    position: absolute;
    top: 216px; right: 48px;
    text-align: left;
    font-size: 15px;
    line-height: 1.45;
    color: var(--ink);
    font-style: normal;
  }

  /* Back */
  .card-back {
    background: linear-gradient(160deg, var(--back-top), var(--back-bottom));
  }
  .back-texture {
    position: absolute; inset: 0;
    background: linear-gradient(160deg, rgba(90,130,200,.35), rgba(40,60,140,.15));
  }
  .back-brand {
    position: absolute;
    top: 120px; left: 0; right: 0;
    text-align: center;
    font-weight: 800;
    font-size: 40px;
    letter-spacing: 2px;
    color: var(--back-text);
    text-transform: uppercase;
  }
  .back-note {
    position: absolute;
    bottom: 34px; left: 50px; right: 50px;
    text-align: center;
    font-size: 14px;
    line-height: 1.55;
    color: var(--back-text);
    letter-spacing: .2px;
  }
  .back-note strong { font-weight: 700; }
</style>
</head>
<body>

  <section class="card card-front" aria-label="Card front">
    <div class="brand-name">Cedar Hollow</div>
    <div class="price">Price $100</div>

    <div class="holder">
      <div class="holder-name">Daniel Brooks</div>
      <div class="holder-role">OWER</div>
    </div>

    <div class="divider"></div>

    <ul class="contacts">
      <li>
        <svg viewBox="0 0 24 24" aria-hidden="true"><path d="M6.6 10.8a15.1 15.1 0 0 0 6.6 6.6l2.2-2.2c.3-.3.7-.4 1-.2 1.1.4 2.3.6 3.6.6.6 0 1 .4 1 1V20c0 .6-.4 1-1 1A17 17 0 0 1 3 4c0-.6.4-1 1-1h3.5c.6 0 1 .4 1 1 0 1.3.2 2.5.6 3.6.1.3 0 .7-.2 1z"/></svg>
        (869) 418 2930
      </li>
      <li>
        <svg viewBox="0 0 24 24" aria-hidden="true"><path d="M7 2h10a2 2 0 0 1 2 2v16a2 2 0 0 1-2 2H7a2 2 0 0 1-2-2V4a2 2 0 0 1 2-2zm0 3v13h10V5zm5 14.2a1 1 0 1 0 0 .1z"/></svg>
        (869) 534 1276
      </li>
      <li>
        <svg viewBox="0 0 24 24" aria-hidden="true"><path d="M3 5h18v14H3zm2 2v.5l7 5 7-5V7l-7 5z"/></svg>
        clearflowbox@mailvista.example
      </li>
      <li>
        <svg viewBox="0 0 24 24" aria-hidden="true"><path d="M12 2a10 10 0 1 0 0 20 10 10 0 0 0 0-20zm0 2c.9 1.2 1.6 2.7 2 4h-4c.4-1.3 1.1-2.8 2-4zM4.3 14a8 8 0 0 1 0-4h3.2a16 16 0 0 0 0 4zm.9 2h2.8c.4 1.3 1 2.6 1.7 3.6A8 8 0 0 1 5.2 16zM8 8H5.2a8 8 0 0 1 4.5-3.6C9 5.4 8.4 6.7 8 8zm4 12c-.9-1.2-1.6-2.7-2-4h4c-.4 1.3-1.1 2.8-2 4zm2.3-6H9.7a14 14 0 0 1 0-4h4.6a14 14 0 0 1 0 4zm.3 5.6c.7-1 1.3-2.3 1.7-3.6h2.8a8 8 0 0 1-4.5 3.6zM16.5 14a16 16 0 0 0 0-4h3.2a8 8 0 0 1 0 4z"/></svg>
        www.cedarhollowwater.example
      </li>
    </ul>

    <address class="address">
      450 Cedar Ridge Road, Ste<br>
      210 Fairview, TN37062
    </address>
  </section>

  <section class="card card-back" aria-label="Card back">
    <div class="back-texture" role="img" aria-label="Repeating embossed brand pattern across the card background"></div>
    <div class="back-brand">Cedar Hollow</div>
    <p class="back-note">
      This card is to be used to access water refills at any Cedar Hollow Water Vending Machines.
      Please contact <strong>(869) 418 2930</strong> or <strong>(869) 534 1276</strong><br>
      or email <strong>clearflowbox@mailvista.example</strong><br>
      for any assistance or recharging of card.
    </p>
  </section>

</body>
</html>
```